WL Bundle Page Redesign Wordpress site

IMPORTANT: the design will need to look nice on mobile...so please keep that in mind!
We need to redesign our current Wordpress page to make it more appealing and look like an ecommerce page. We need the ability to implement this design on our Wordpress site.
Here is the current page: https://www.rlpalmerhealth.com/supplements/weight-loss-focus-bundle/
However, the reference sample of what it has to look like or complement is also attached.
Attached is the Word document is the copy for the new page and the FAQs text.
The color palette should match the bottles or look nice with all 3 bottles on the page.
Thanks!

Requirements
Should not have
• any random stock photography; use images provided

```html
<!DOCTYPE html>
<html lang="en">
<head>
<meta charset="utf-8">
<title>Nora Vale – Weight Loss Focus Bundle</title>
<link href="https://fonts.googleapis.com/css2?family=Poppins:wght@400;500;600;700;800&family=Roboto:wght@400;500;700&display=swap" rel="stylesheet">
<style>
:root{
  --coral:#f37381;
  --coral-deep:#ec5a6b;
  --coral-soft:#fbd3d8;
  --red:#e2344c;
  --navy:#1f2542;
  --ink:#4a4f63;
  --muted:#8a8fa3;
  --line:#f2c7cd;
  --white:#ffffff;
  --grey-bg:#f4f4f6;
}
*{box-sizing:border-box;margin:0;padding:0}
html,body{width:1200px;height:3700px;overflow:hidden;background:var(--white)}
body{font-family:"Roboto",sans-serif;color:var(--ink);position:relative}
.abs{position:absolute}
h1,h2,h3,.display{font-family:"Poppins",sans-serif}

/* hero */
.hero{position:absolute;left:0;top:0;width:1200px;height:585px;background:linear-gradient(180deg,#f58592 0%,var(--coral) 100%);overflow:hidden}
.nav{left:155px;top:22px;width:890px;height:56px;background:var(--white);border-radius:8px;display:flex;align-items:center;padding:0 22px;box-shadow:0 4px 14px rgba(0,0,0,.06)}
.brand{display:flex;align-items:center;gap:8px;font-family:"Poppins",sans-serif;font-weight:700;font-size:17px;color:var(--navy);letter-spacing:.5px}
.brand-dot{width:10px;height:10px;border-radius:50%;background:var(--coral)}
.nav-links{margin-left:auto;display:flex;gap:28px;font-size:12px;color:var(--navy)}
.nav-cta{margin-left:26px;background:var(--coral);color:#fff;font-size:12px;padding:8px 18px;border-radius:20px}
.nav-login{margin-left:12px;font-size:12px;color:var(--navy);border:1px solid #ddd;padding:7px 14px;border-radius:20px}
.ghost-title{left:130px;top:215px;font-family:"Poppins",sans-serif;font-weight:800;font-size:120px;line-height:1;color:rgba(255,255,255,.12);white-space:nowrap;letter-spacing:2px}
.hero-kicker{left:155px;top:166px;color:#fff;font-weight:600;font-size:13px;letter-spacing:1px}
.hero-title{left:155px;top:186px;color:#fff;font-weight:800;font-size:36px;line-height:1.2;letter-spacing:1px;white-space:nowrap}
.hero-tag{left:155px;top:258px;width:320px;background:rgba(255,255,255,.92);padding:10px 14px;font-family:"Poppins",sans-serif;font-size:21px;line-height:1.25;color:var(--coral-deep);font-weight:500}
.hero-tag b{color:var(--red)}
.rating{left:155px;top:380px;display:flex;align-items:center;gap:8px;color:#fff;font-size:13px}
.stars{color:#ffd54a;letter-spacing:2px;font-size:15px}
.bottle{left:535px;top:110px;width:175px;height:275px;border-radius:34px 34px 22px 22px;background:linear-gradient(160deg,#ffffff 0%,#f7e9ec 60%,#e9c9cf 100%);transform:rotate(18deg);box-shadow:0 20px 40px rgba(120,20,40,.25)}
.plans{left:770px;top:345px;display:flex;gap:10px}
.plan{display:flex;align-items:center;gap:7px;background:#fff;color:var(--navy);font-size:11px;font-weight:500;padding:8px 14px;border-radius:22px}
.plan.alt{background:transparent;color:#fff;border:1px solid rgba(255,255,255,.7)}
.plan i{width:12px;height:12px;border-radius:50%;border:3px solid var(--coral);display:block}
.price{left:770px;top:400px;color:#fff}
.price small{display:block;font-size:13px;font-weight:600;letter-spacing:.5px}
.price s{font-size:14px;opacity:.8;margin-right:8px}
.price strong{font-family:"Poppins",sans-serif;font-size:30px;font-weight:700}
.cart{left:735px;top:508px;background:var(--red);color:#fff;font-size:12px;font-weight:600;padding:10px 22px;border-radius:22px}
.stock{left:870px;top:518px;color:#fff;font-size:12px;font-weight:500}

/* media strip */
.media{left:155px;top:600px;width:890px;height:66px;background:#fff;border-radius:6px;box-shadow:0 6px 20px rgba(0,0,0,.07);display:flex;align-items:center;justify-content:space-around;padding:0 20px}
.media span{display:block;height:22px;background:#2a2d38;border-radius:3px}

/* product rows */
.photo{border-radius:10px}
.kicker{font-size:14px;font-weight:500;color:var(--navy);letter-spacing:.8px;text-transform:uppercase}
.ptitle{font-weight:800;font-size:36px;color:var(--coral-deep);letter-spacing:.5px;line-height:1.1;margin-top:4px}
.intro{font-size:11.5px;color:var(--ink);margin-top:18px}
.intro b{color:var(--navy)}
.bullets{list-style:none;margin-top:12px}
.bullets li{display:flex;gap:9px;align-items:flex-start;font-size:11px;line-height:1.45;color:var(--muted);margin-bottom:10px}
.bullets li::before{content:"";flex:0 0 7px;height:7px;border-radius:50%;background:var(--coral);margin-top:4px}
.cards{display:flex;gap:16px}
.card{border:1.5px solid var(--line);border-radius:12px;background:#fff;display:flex;flex-direction:column;align-items:center;justify-content:center;text-align:center;gap:12px;font-size:11.5px;color:var(--navy);padding:0 8px}
.card svg{width:38px;height:38px}
.divider{height:1px;background:#ececf0}

/* testimonials */
.reviews{left:0;top:2865px;width:1200px;height:560px;background:var(--grey-bg)}
.sec-kicker{width:1200px;text-align:center;font-size:13px;color:var(--navy);letter-spacing:.8px;text-transform:uppercase}
.sec-title{width:1200px;text-align:center;font-weight:800;font-size:34px;color:var(--navy);letter-spacing:1px}
.sec-bar{left:575px;width:50px;height:3px;background:var(--coral)}
.video{width:208px;height:370px;border-radius:12px;overflow:hidden}
.play{left:50%;top:50%;width:44px;height:44px;margin:-22px 0 0 -22px;border-radius:50%;background:#fff;display:flex;align-items:center;justify-content:center}
.ba{height:160px;border-radius:8px}
</style>
</head>
<body>

<!-- HERO -->
<section class="hero">
  <div class="abs ghost-title">BELLY BALANCE</div>
  <nav class="abs nav">
    <div class="brand"><span class="brand-dot"></span>NORA VALE</div>
    <div class="nav-links"><span>Success Stories</span><span>Meet Nora</span><span>About</span><span>Blogs</span></div>
    <span class="nav-cta">Get Started</span>
    <span class="nav-login">Login</span>
  </nav>
  <div class="abs hero-kicker">DETOX &amp; FAT METABOLISM</div>
  <h1 class="abs hero-title">BELLY BALANCE</h1>
  <p class="abs hero-tag">Is an <b>Oxygenating</b> Colon Cleansing <b>Formula</b> Designed</p>
  <div class="abs rating"><span class="stars">★★★★★</span>4.9 (378 Reviews)</div>
  <div class="abs bottle" role="img" aria-label="Belly Balance supplement bottle"></div>
  <div class="abs plans">
    <span class="plan"><i></i>30 Day Purchase</span>
    <span class="plan alt"><i style="border-color:#fff"></i>Subscribe and Save 15%</span>
  </div>
  <div class="abs price"><small>PRICE FOR BUNDLE:</small><s>$144.99</s><strong>$99.99</strong></div>
  <span class="abs cart">Add to Cart</span>
  <span class="abs stock">In Stock &amp; Ready To Ship</span>
</section>

<div class="abs media" aria-label="As seen in">
  <span style="width:80px"></span><span style="width:40px"></span><span style="width:52px"></span>
  <span style="width:36px;height:30px;border-radius:50%"></span><span style="width:60px"></span>
  <span style="width:66px"></span><span style="width:120px"></span><span style="width:56px;background:var(--red)"></span>
</div>

<!-- LIVER -->
<div class="abs photo" style="left:155px;top:790px;width:300px;height:215px;background:linear-gradient(135deg,#f6c9d3,#f9e4ea 60%,#f1b6c2)" role="img" aria-label="Smiling woman in pink holding a Liver Renew bottle"></div>
<div class="abs" style="left:600px;top:800px;width:440px">
  <div class="kicker">Detox &amp; Fat Metabolism</div>
  <h2 class="ptitle">LIVER RENEW</h2>
  <p class="intro"><b>Liver Renew</b> is a premium liver cleanser and detox formula to:</p>
  <ul class="bullets">
    <li>Support your liver health with an all-natural cleanse blend</li>
    <li>Naturally increase your body's fat burning capabilities</li>
    <li>Help your body defend against harmful toxins found in everyday living</li>
    <li>Help your overworked liver feel its best while you focus on weight loss</li>
  </ul>
</div>
<div class="abs cards" style="left:280px;top:1135px">
  <div class="card" style="width:200px;height:150px"><svg viewBox="0 0 40 40" fill="none" stroke="var(--coral)" stroke-width="2"><path d="M20 5c4 7 11 11 11 20a11 11 0 0 1-22 0c0-6 4-9 5-13 2 3 3 5 6 5 0-4-2-8 0-12z"/></svg>Incremental Fat Burning</div>
  <div class="card" style="width:200px;height:150px"><svg viewBox="0 0 40 40" fill="none" stroke="var(--coral)" stroke-width="2"><circle cx="20" cy="20" r="15"/><path d="M20 12v16M12 20h16"/></svg>Support Liver Health</div>
  <div class="card" style="width:200px;height:150px"><svg viewBox="0 0 40 40" fill="none" stroke="var(--coral)" stroke-width="2"><circle cx="20" cy="20" r="7"/><path d="M20 5v6M20 29v6M5 20h6M29 20h6M9 9l4 4M27 27l4 4M31 9l-4 4M13 27l-4 4"/></svg>Protect Against Toxins</div>
</div>

<div class="abs divider" style="left:155px;top:1345px;width:890px"></div>

<!-- BLOOD SUGAR -->
<div class="abs" style="left:155px;top:1455px;width:430px">
  <div class="kicker">Stabilize &amp; Support Fat Loss</div>
  <h2 class="ptitle" style="color:var(--red)">GLUCOSE BALANCE</h2>
  <p class="intro"><b>Glucose Balance</b> has Clinically-Studied Ingredients for Natural Weight Loss designed:</p>
  <ul class="bullets">
    <li>To healthy fat loss and reduction of body weight, including visceral belly fat</li>
    <li>To support healthy insulin sensitivity so your body uses glucose well</li>
    <li>To stabilize blood sugar levels so cravings stop and energy stays steady</li>
    <li>For anyone who wants help managing weight as part of a healthy lifestyle</li>
  </ul>
</div>
<div class="abs photo" style="left:630px;top:1485px;width:415px;height:295px;background:linear-gradient(135deg,#e4ddf3,#cfc6ec 60%,#f3c2d7)" role="img" aria-label="Smiling woman in a pink blazer holding a Glucose Balance bottle"></div>
<div class="abs cards" style="left:155px;top:1825px">
  <div class="card" style="width:165px;height:135px"><svg viewBox="0 0 40 40" fill="none" stroke="var(--navy)" stroke-width="2"><circle cx="20" cy="20" r="4"/><circle cx="8" cy="10" r="3"/><circle cx="32" cy="10" r="3"/><circle cx="8" cy="30" r="3"/><circle cx="32" cy="30" r="3"/><path d="M11 12l6 6M29 12l-6 6M11 28l6-6M29 28l-6-6"/></svg>Healthy Sugar &amp; Carb Absorption</div>
  <div class="card" style="width:165px;height:135px"><svg viewBox="0 0 40 40" fill="none" stroke="var(--navy)" stroke-width="2"><path d="M8 32l24-24M24 8h8v8M10 24l6 6"/></svg>Normal Insulin Sensitivity</div>
  <div class="card" style="width:165px;height:135px"><svg viewBox="0 0 40 40" fill="var(--navy)"><path d="M20 34S5 25 5 14a8 8 0 0 1 15-4 8 8 0 0 1 15 4c0 11-15 20-15 20z"/></svg>Healthy Inflammation Response</div>
  <div class="card" style="width:165px;height:135px"><svg viewBox="0 0 40 40" fill="none" stroke="var(--navy)" stroke-width="2"><circle cx="20" cy="20" r="14"/><circle cx="16" cy="17" r="4"/><circle cx="25" cy="25" r="2"/></svg>Healthy Cell Function</div>
  <div class="card" style="width:165px;height:135px"><svg viewBox="0 0 40 40" fill="none" stroke="var(--navy)" stroke-width="2"><rect x="8" y="10" width="24" height="24" rx="4"/><path d="M15 18h10M20 14v8"/></svg>Healthy Weight Management</div>
</div>

<div class="abs divider" style="left:155px;top:2050px;width:890px"></div>

<!-- BELLY -->
<div class="abs photo" style="left:155px;top:2175px;width:300px;height:280px;background:linear-gradient(135deg,#f27c88,#f59aa4 60%,#f7b8c0)" role="img" aria-label="Smiling woman in white and pink holding a Belly Balance bottle"></div>
<div class="abs" style="left:600px;top:2215px;width:440px">
  <div class="kicker">Gut Health &amp; Digestive Cleansing</div>
  <h2 class="ptitle">BELLY BALANCE</h2>
  <p class="intro"><b>Belly Balance</b> is an oxygenating colon cleansing formula designed to:</p>
  <ul class="bullets">
    <li>Aid in cleansing the digestive tract</li>
    <li>Improve digestion and support gut health</li>
    <li>Help to move regularity and relieve occasional constipation</li>
    <li>Promote the elimination of harmful bacteria in the gut</li>
  </ul>
</div>
<div class="abs cards" style="left:155px;top:2515px">
  <div class="card" style="width:165px;height:150px"><svg viewBox="0 0 40 40" fill="none" stroke="var(--coral)" stroke-width="2"><path d="M10 6v10a6 6 0 0 0 6 6h8a6 6 0 0 1 6 6v6M30 6v8"/></svg>Colon Cleanse</div>
  <div class="card" style="width:165px;height:150px"><svg viewBox="0 0 40 40" fill="none" stroke="var(--coral)" stroke-width="2"><path d="M14 6c0 8 12 6 12 14s-12 6-12 14"/><path d="M26 6c0 4-3 5-6 6"/></svg>Improves Digestion</div>
  <div class="card" style="width:165px;height:150px"><svg viewBox="0 0 40 40" fill="none" stroke="var(--coral)" stroke-width="2"><rect x="8" y="8" width="24" height="24" rx="8"/><path d="M14 20h12"/></svg>Supports Gut Health</div>
  <div class="card" style="width:165px;height:150px"><svg viewBox="0 0 40 40" fill="none" stroke="var(--coral)" stroke-width="2"><path d="M12 34V14a8 8 0 0 1 16 0v20"/><path d="M16 22h8"/></svg>Promotes Regularity</div>
  <div class="card" style="width:165px;height:150px"><svg viewBox="0 0 40 40" fill="none" stroke="var(--coral)" stroke-width="2"><rect x="10" y="6" width="20" height="28" rx="4"/><path d="M15 20l4 4 7-8"/></svg>Natural Constipation Relief</div>
</div>

<!-- REVIEWS -->
<section class="abs reviews">
  <div class="abs sec-kicker" style="left:0;top:40px">What People Say About</div>
  <h2 class="abs sec-title display" style="left:0;top:58px">OUR PRODUCTS</h2>
  <div class="abs sec-bar" style="top:110px"></div>
  <svg class="abs" style="left:940px;top:45px" width="60" height="50" viewBox="0 0 60 50" fill="none" stroke="#d5d6de" stroke-width="2"><rect x="4" y="6" width="44" height="30" rx="5"/><path d="M14 36v10l10-10"/><path d="M14 18h24M14 26h16"/></svg>
  <div class="abs video" style="left:155px;top:140px;background:linear-gradient(180deg,#6b5a52,#2e2726)" role="img" aria-label="Customer video testimonial"><div class="abs play"><svg width="14" height="16" viewBox="0 0 14 16"><path d="M2 1l11 7-11 7z" fill="var(--coral)"/></svg></div></div>
  <div class="abs video" style="left:382px;top:140px;background:linear-gradient(180deg,#b9a79d,#5a4a44)" role="img" aria-label="Customer video testimonial"><div class="abs play"><svg width="14" height="16" viewBox="0 0 14 16"><path d="M2 1l11 7-11 7z" fill="var(--coral)"/></svg></div></div>
  <div class="abs video" style="left:609px;top:140px;background:linear-gradient(180deg,#8d7e76,#3b3330)" role="img" aria-label="Customer video testimonial"><div class="abs play"><svg width="14" height="16" viewBox="0 0 14 16"><path d="M2 1l11 7-11 7z" fill="var(--coral)"/></svg></div></div>
  <div class="abs video" style="left:837px;top:140px;background:linear-gradient(180deg,#c8bdb6,#6e625c)" role="img" aria-label="Customer video testimonial"><div class="abs play"><svg width="14" height="16" viewBox="0 0 14 16"><path d="M2 1l11 7-11 7z" fill="var(--coral)"/></svg></div></div>
</section>

<!-- BEFORE AFTER -->
<div class="abs sec-kicker" style="left:0;top:3455px">Before – After</div>
<h2 class="abs sec-title display" style="left:0;top:3472px">LOVING THEIR RESULTS</h2>
<div class="abs sec-bar" style="top:3524px"></div>
<div class="abs ba" style="left:155px;top:3555px;width:200px;background:linear-gradient(135deg,#9fb4a0,#d9d2c4)" role="img" aria-label="Customer before and after photos"></div>
<div class="abs ba" style="left:380px;top:3555px;width:200px;background:linear-gradient(135deg,#c7b8ad,#e8e2dc)" role="img" aria-label="Customer before and after photos"></div>
<div class="abs ba" style="left:610px;top:3555px;width:200px;background:linear-gradient(135deg,#b0a49e,#ded6d0)" role="img" aria-label="Customer before and after photos"></div>
<div class="abs ba" style="left:840px;top:3555px;width:205px;background:linear-gradient(135deg,#f2a3ad,#f6d1d6)" role="img" aria-label="Customer before and after photos"></div>

</body>
</html>
```